Holiday Rental Company Flyer Design (DL not A5)

Note from Brandloom Administration: The category sizing selected is A5, however the project requires DL sized artwork. Please refer to the DL template link below while the 'Special Requirements' are updated accordingly.

Project Brief:
We need a double sided DL flyer designed for an up market Holiday Rental Company that portrays a personalised approach to property management. These are to be used for letter box drops to homes we're specifically targeting so the design should be modern, complimentary colour palette, uncluttered & visually appealing.

Please Download the DL Template from Quillora here: http://www.quillora.com.au/ql/ns/propath/UploadResources.aspx?selectedTab=0?pfid=KMT&pf_id=KMT&xnav=easypath-upload-image#Templates

Target Market(s)

Wealthy Home Owners

Industry/Entity Type

It Company

Other font styles liked:
• Avant Garde Extra Light & Demi

Colors
33b8a4

Requirements
Must have
• DL Flyer sizes (210mm width x 99mm width, plus 3mm bleed)
• Front: Logo, Main Image & Grab
• Back: Contact Details & Brief Description of our business
• Images: Ideally the main image should be the house with the pool but alternatively a lifestyle images could also be used.
Nice to have
• A creative designer!
Should not have
• Clutter & busy designs

```html
<!DOCTYPE html>
<html lang="en">
<head>
<meta charset="utf-8">
<title>Coastline Retreats – DL Flyer</title>
<link href="https://fonts.googleapis.com/css2?family=Questrial&display=swap" rel="stylesheet">
<style>
  :root {
    --green: #63b08f;
    --green-light: #9fd2c0;
    --charcoal: #4a4743;
    --sand: #e9e6e0;
    --ink: #1e1e1e;
    --grey-text: #555350;
    --logo-teal: #86cdb3;
    --white: #ffffff;
    --page: #ffffff;
  }
  html, body {
    margin: 0;
    padding: 0;
    overflow: hidden;
    background: var(--page);
  }
  .canvas {
    position: relative;
    width: 1153px;
    height: 1200px;
    overflow: hidden;
    font-family: "Questrial", "Century Gothic", sans-serif;
  }
  .card {
    position: absolute;
    left: 36px;
    width: 1063px;
    height: 500px;
    overflow: hidden;
  }
  .card--front { top: 126px; }
  .card--back { top: 692px; background: var(--sand); }
  .card__shapes {
    position: absolute;
    inset: 0;
    width: 100%;
    height: 100%;
  }
  .front-title {
    position: absolute;
    left: 20px;
    top: 12px;
    margin: 0;
    font-weight: 400;
    color: var(--white);
    line-height: 1;
  }
  .front-title__main { display: block; font-size: 36px; letter-spacing: 0.2px; }
  .front-title__sub { display: block; font-size: 25px; color: var(--charcoal); margin-top: 4px; }
  .front-title__sub strong { font-weight: 700; }
  .brand {
    position: absolute;
    left: 820px;
    top: 46px;
    display: flex;
    align-items: center;
    gap: 12px;
  }
  .brand__dot {
    width: 40px;
    height: 40px;
    border-radius: 50%;
    background: var(--logo-teal);
  }
  .brand__name {
    font-size: 25px;
    line-height: 1.05;
    letter-spacing: 1.5px;
    color: var(--logo-teal);
    text-transform: uppercase;
  }
  .back-heading {
    position: absolute;
    right: 15px;
    top: 14px;
    margin: 0;
    font-size: 27px;
    font-weight: 400;
    color: var(--white);
    letter-spacing: 0.3px;
  }
  .intro {
    position: absolute;
    left: 20px;
    top: 30px;
    width: 600px;
    margin: 0;
    font-size: 16px;
    line-height: 28px;
    font-style: italic;
    letter-spacing: 1.6px;
    word-spacing: 3px;
    color: var(--grey-text);
  }
  .service {
    position: absolute;
    left: 20px;
    top: 140px;
    width: 1030px;
    margin: 0;
    font-size: 19px;
    color: var(--ink);
  }
  .service strong { font-weight: 700; }
  .benefits {
    position: absolute;
    left: 56px;
    top: 188px;
    margin: 0;
    padding: 0;
    list-style: none;
    font-size: 19px;
    color: var(--ink);
  }
  .benefits li {
    position: relative;
    padding-left: 30px;
    height: 47px;
  }
  .benefits li::before {
    content: "";
    position: absolute;
    left: 0;
    top: 7px;
    width: 10px;
    height: 10px;
    background: var(--charcoal);
  }
  .contact-cta {
    position: absolute;
    left: 397px;
    top: 342px;
    display: flex;
    gap: 20px;
    align-items: flex-start;
  }
  .contact-cta__label {
    margin: 0;
    font-size: 26px;
    font-weight: 700;
    color: var(--charcoal);
    white-space: nowrap;
  }
  .contact-cta__note {
    margin: 4px 0 0;
    font-size: 16px;
    line-height: 23px;
    font-style: italic;
    letter-spacing: 1.2px;
    color: var(--grey-text);
  }
  .contact-details {
    position: absolute;
    left: 15px;
    top: 402px;
    margin: 0;
    font-style: normal;
    font-size: 18px;
    line-height: 22px;
    color: var(--white);
  }
</style>
</head>
<body>
<main class="canvas">

  <section class="card card--front" aria-label="Flyer front">
    <svg class="card__shapes" viewBox="0 0 837 394" preserveAspectRatio="none" aria-hidden="false">
      <defs>
        <linearGradient id="pool-scene" x1="0" y1="0" x2="0" y2="1">
          <stop offset="0" stop-color="#c9d9e6"/>
          <stop offset="0.35" stop-color="#eeeae2"/>
          <stop offset="0.55" stop-color="#6fa6a8"/>
          <stop offset="1" stop-color="#2f7f86"/>
        </linearGradient>
      </defs>
      <rect x="0" y="40" width="837" height="320" fill="url(#pool-scene)" role="img" aria-label="Photo of a modern single-storey house with a blue swimming pool, spa and desert plants"/>
      <polygon class="band band--green" points="0,0 800,0 420,50 0,78" fill="var(--green)"/>
      <polygon class="band band--charcoal" points="420,50 837,0 837,140 720,118" fill="var(--charcoal)"/>
      <polygon class="band band--green" points="0,338 837,322 837,394 0,394" fill="var(--green)"/>
      <polygon class="band band--light" points="280,394 837,330 837,394" fill="var(--green-light)"/>
    </svg>
    <h1 class="front-title">
      <span class="front-title__main">Holiday Rental Management</span>
      <span class="front-title__sub">with a <strong>difference</strong></span>
    </h1>
    <div class="brand">
      <span class="brand__dot"></span>
      <span class="brand__name">Coastline<br>Retreats</span>
    </div>
  </section>

  <section class="card card--back" aria-label="Flyer back">
    <svg class="card__shapes" viewBox="0 0 837 394" preserveAspectRatio="none" aria-hidden="true">
      <polygon class="band band--charcoal" points="0,0 837,0 837,45 590,45 0,5" fill="var(--charcoal)"/>
      <polygon class="band band--green" points="0,280 837,395 0,395" fill="var(--green)"/>
      <polygon class="band band--light" points="620,395 837,338 837,395" fill="var(--green-light)"/>
    </svg>
    <h2 class="back-heading">What we do differently</h2>
    <p class="intro">Rather than relying upon a key safe or a central pickup destination, a Coastline Retreats staff member will greet guests upon arrival.</p>
    <p class="service">Our <strong>‘Meet &amp; Greet’</strong> service provides home owners with an increased level of Security and also allows us to:</p>
    <ul class="benefits">
      <li>Prepare the home for their arrival (lights, heaters, music etc.).</li>
      <li>Establish a rapport &amp; help facilitate future bookings.</li>
      <li>Reiterate their responsibilities to ensure the return of their bond.</li>
    </ul>
    <div class="contact-cta">
      <p class="contact-cta__label">Contact us on</p>
      <p class="contact-cta__note">If you’d like to know what your property<br>could achieve or require additional information</p>
    </div>
    <address class="contact-details">
      (03) 5900 1234<br>
      PO Box 12, Harbourvale Victoria 3900<br>
      stay@coastlineretreats.com.au<br>
      coastlineretreats.com.au
    </address>
  </section>

</main>
</body>
</html>
```